Need CATCHY/VIVID Banner design for my new UTV/ATV/Off Road Vehicle turn signal/lighting company

I need a banner ad designed so I can advertise on several different ATV (all terrain vehicle), UTV (Utility Vehicles), Golf Cart and Off-Road Vehicle forums. Ads need to be very catchy and produce a call to action. Action is getting hits to my website. Our main business is selling turn signal kits to make your side by side or your ATV/UTV street legal, as some states now allow you to drive these on public roads if you have the following items: Turn Signals, Horn, Lighted license plate bracket, headlights and brake lights. We sell all of these items for just about any model vehicle out there. Our call to action for this banner would be to get more website visits.

Target Market(s)

Off-road/outdoor enthusiasts,

Industry/Entity Type

Car Accessorie

Font styles to use
Sans Serif

Requirements
Must have
• Ad size need to be either 728x90 or 300x250. Colorful ad with an off-road vehicle integrated to the design (think UTV, side-by-side, etc.
Nice to have
• Nice to haves would be anything that makes this banner ad stand out on very boring web pages.
Should not have
• anything dull

```html
<!DOCTYPE html>
<html lang="en">
<head>
<meta charset="utf-8">
<title>Trailbeam Signal Kits – ATV &amp; UTV Banner</title>
<link rel="stylesheet" href="https://fonts.googleapis.com/css2?family=Roboto+Condensed:wght@700;800&display=swap">
<style>
  :root {
    --red-deep: #2b070b;
    --red-mid: #9a0f18;
    --red-bright: #e3232b;
    --yellow: #ffbf12;
    --yellow-warm: #f7a600;
    --white: #ffffff;
    --ink: #1a1a1a;
  }
  * { margin: 0; padding: 0; box-sizing: border-box; }
  html, body { width: 1200px; height: 1000px; overflow: hidden; background: #fff; }
  .banner {
    position: relative;
    width: 1200px;
    height: 1000px;
    overflow: hidden;
    font-family: "Roboto Condensed", "Arial Narrow", sans-serif;
    background: linear-gradient(115deg, var(--red-deep) 0%, #5a0a10 30%, var(--red-mid) 55%, var(--red-bright) 100%);
  }
  .shapes { position: absolute; inset: 0; }
  .brand {
    position: absolute;
    left: 36px;
    top: 36px;
    display: flex;
    align-items: center;
    gap: 24px;
    color: var(--white);
    font-weight: 800;
    text-transform: uppercase;
  }
  .brand-dot {
    width: 210px; height: 130px;
    display: flex; align-items: center; justify-content: center;
  }
  .brand-dot span {
    width: 110px; height: 110px; border-radius: 50%;
    background: var(--white);
  }
  .brand-name { line-height: 1; }
  .brand-name .line-main { font-size: 44px; letter-spacing: 1px; display: block; }
  .brand-name .line-sub { font-size: 30px; letter-spacing: 1px; display: block; margin-top: 6px; }
  .vehicle-photo {
    position: absolute;
    left: 640px;
    top: 250px;
    width: 560px;
    height: 620px;
    border-radius: 40px 0 0 40px;
    background: radial-gradient(ellipse at 55% 55%, #3a3a3c 0%, #1d1d1f 55%, rgba(20,20,22,0.85) 100%);
  }
  .headline {
    position: absolute;
    left: 40px;
    top: 440px;
    color: var(--white);
    font-weight: 800;
    font-size: 92px;
    line-height: 1.0;
    letter-spacing: 1px;
    text-transform: uppercase;
  }
  .subhead {
    position: absolute;
    left: 40px;
    top: 636px;
    color: var(--yellow);
    font-weight: 800;
    font-size: 54px;
    line-height: 1.1;
    letter-spacing: 1.5px;
    text-transform: uppercase;
  }
  .feature-icons {
    position: absolute;
    left: 52px;
    top: 800px;
    display: flex;
    gap: 16px;
    list-style: none;
  }
  .feature-icons li {
    width: 126px; height: 126px; border-radius: 50%;
    background: var(--yellow);
    display: flex; align-items: center; justify-content: center;
  }
  .feature-icons svg { width: 80px; height: 80px; }
</style>
</head>
<body>
<div class="banner">
  <svg class="shapes" viewBox="0 0 1200 1000" aria-hidden="true">
    <polygon points="780,170 1200,170 1200,250 1040,420 640,420" fill="var(--yellow)" opacity="0.95"/>
    <polygon points="640,420 960,420 760,780 580,780" fill="var(--yellow-warm)"/>
    <polygon points="1060,120 1200,120 1200,160 1030,160" fill="var(--yellow)" opacity="0.6"/>
  </svg>

  <div class="brand">
    <div class="brand-dot"><span></span></div>
    <div class="brand-name">
      <span class="line-main">Trailbeam Signal Kits</span>
      <span class="line-sub">&amp; Lighting Accessories</span>
    </div>
  </div>

  <div class="vehicle-photo" role="img" aria-label="Photo of a black side-by-side utility vehicle with roof and winch, angled toward the viewer"></div>

  <h1 class="headline">ATV &amp; UTV<br>Vechicle</h1>
  <p class="subhead">Signal Kits<br>and Lighting</p>

  <ul class="feature-icons">
    <li aria-label="Brake lights">
      <svg viewBox="0 0 80 80" fill="none" stroke="var(--white)" stroke-width="5" stroke-linecap="round">
        <circle cx="40" cy="40" r="20"/>
        <path d="M16 22a30 30 0 0 0 0 36M64 22a30 30 0 0 1 0 36"/>
        <line x1="40" y1="30" x2="40" y2="43"/>
        <circle cx="40" cy="51" r="1.5" fill="var(--white)"/>
      </svg>
    </li>
    <li aria-label="Headlights">
      <svg viewBox="0 0 80 80" fill="none" stroke="var(--white)" stroke-width="5" stroke-linecap="round">
        <path d="M40 22c-14 0-18 9-18 18s4 18 18 18z" fill="var(--white)"/>
        <line x1="48" y1="26" x2="66" y2="26"/>
        <line x1="48" y1="36" x2="66" y2="36"/>
        <line x1="48" y1="46" x2="66" y2="46"/>
        <line x1="48" y1="56" x2="66" y2="56"/>
      </svg>
    </li>
    <li aria-label="Horn">
      <svg viewBox="0 0 80 80" fill="var(--white)" stroke="var(--white)" stroke-width="4" stroke-linecap="round">
        <path d="M14 36h14l24-12v32L28 44H14z"/>
        <rect x="10" y="34" width="6" height="12" rx="2"/>
        <line x1="60" y1="30" x2="70" y2="24" fill="none"/>
        <line x1="60" y1="40" x2="72" y2="40" fill="none"/>
        <line x1="60" y1="50" x2="70" y2="56" fill="none"/>
      </svg>
    </li>
    <li aria-label="Turn signals">
      <svg viewBox="0 0 80 80" fill="none" stroke="var(--white)" stroke-width="5" stroke-linejoin="round">
        <path d="M8 40l14-14v8h36v-8l14 14-14 14v-8H22v8z"/>
      </svg>
    </li>
  </ul>
</div>
</body>
</html>
```